Specialised investor in e-mobility and energy wants business card design

We need a business card design that fits our existing corporate design. <The look and feel must be 'sharp'/'clean', dynamic, communicate momentum, professionalism etc (as one would imagine from a firm in the financial sector). We like the idea of a reverse-side of the card that includes the logo, and the name and contact details on the other. We expect the deliverable to be whatever format might be required to be able to get cards printed directly by a service such as kelmo press. Our website is www.zub.capital

```html
<!DOCTYPE html>
<html lang="en">
<head>
<meta charset="utf-8">
<title>Zub Capital – Business Card</title>
<link href="https://fonts.googleapis.com/css2?family=Jost:wght@400;500;600&display=swap" rel="stylesheet">
<style>
  :root {
    --backdrop: #dcdddf;
    --card-white: #ffffff;
    --brand-green: #8cc43f;
    --brand-green-deep: #74ab2e;
    --brand-dark: #2f5d1f;
    --text-grey: #3a3a3a;
    --rule: #b9b39a;
  }
  * { margin: 0; padding: 0; box-sizing: border-box; }
  html, body { width: 1200px; height: 800px; overflow: hidden; }
  body {
    background: var(--backdrop);
    font-family: "Jost", sans-serif;
    position: relative;
  }
  .card {
    position: absolute;
    top: 245px;
    width: 540px;
    height: 309px;
    box-shadow: 0 8px 24px rgba(0,0,0,0.12);
  }
  .card--back {
    left: 40px;
    background: linear-gradient(120deg, var(--brand-green-deep) 0%, var(--brand-green) 55%, #9ccf55 100%);
  }
  .card--front {
    left: 620px;
    background: var(--card-white);
  }
  .wordmark {
    position: absolute;
    display: flex;
    align-items: center;
    gap: 12px;
    font-weight: 500;
    letter-spacing: 0.5px;
  }
  .wordmark__mark { display: block; }
  .card--back .wordmark {
    left: 170px; top: 130px;
    font-size: 44px;
    color: var(--card-white);
  }
  .card--back .wordmark__mark { width: 22px; height: 22px; background: var(--card-white); }
  .card--front .wordmark {
    right: 34px; top: 40px;
    font-size: 34px;
    color: var(--brand-dark);
  }
  .card--front .wordmark__mark { width: 18px; height: 18px; background: var(--brand-green); }
  .person {
    position: absolute;
    left: 40px; top: 130px;
  }
  .person__name {
    font-weight: 600;
    font-size: 15px;
    letter-spacing: 0.6px;
    color: var(--brand-green);
    text-transform: uppercase;
  }
  .person__role {
    font-weight: 500;
    font-size: 13px;
    color: var(--brand-dark);
  }
  .person__rule {
    position: absolute;
    left: 40px; top: 176px;
    width: 300px; height: 1px;
    background: var(--rule);
  }
  .contacts {
    position: absolute;
    left: 40px; top: 196px;
    display: flex;
    gap: 18px;
  }
  .contacts__group {
    display: flex;
    flex-direction: column;
    gap: 8px;
  }
  .contacts__group + .contacts__group {
    border-left: 1px solid var(--rule);
    padding-left: 18px;
  }
  .contact {
    display: flex;
    align-items: center;
    gap: 8px;
    font-size: 13px;
    color: var(--text-grey);
  }
  .contact svg { width: 13px; height: 13px; flex: none; }
</style>
</head>
<body>

  <section class="card card--back" aria-label="Card reverse side">
    <div class="wordmark"><span class="wordmark__mark"></span>Zub Capital</div>
  </section>

  <section class="card card--front" aria-label="Card front side">
    <div class="wordmark"><span class="wordmark__mark"></span>Zub Capital</div>

    <div class="person">
      <p class="person__name">Mara Ellison</p>
      <p class="person__role">Partner</p>
    </div>
    <div class="person__rule"></div>

    <div class="contacts">
      <div class="contacts__group">
        <p class="contact">
          <svg viewBox="0 0 14 14" aria-hidden="true"><rect x="3.5" y="1" width="7" height="12" rx="1.2" fill="none" stroke="#2f5d1f" stroke-width="1.3"/><circle cx="7" cy="11" r="0.8" fill="#2f5d1f"/></svg>
          +41 79 555 0142
        </p>
        <p class="contact">
          <svg viewBox="0 0 14 14" aria-hidden="true"><path d="M7 13 C3 8 2.5 6.5 2.5 5 A4.5 4.5 0 0 1 11.5 5 C11.5 6.5 11 8 7 13Z" fill="#2f5d1f"/><circle cx="7" cy="5" r="1.6" fill="#fff"/></svg>
          Lucerne, Switzerland
        </p>
      </div>
      <div class="contacts__group">
        <p class="contact">
          <svg viewBox="0 0 14 14" aria-hidden="true"><rect x="1" y="3" width="12" height="8.5" rx="1" fill="#2f5d1f"/><path d="M1.5 3.5 L7 8 L12.5 3.5" fill="none" stroke="#fff" stroke-width="1.1"/></svg>
          mara@zub.capital
        </p>
        <p class="contact">
          <svg viewBox="0 0 14 14" aria-hidden="true"><circle cx="7" cy="7" r="5.6" fill="none" stroke="#2f5d1f" stroke-width="1.3"/><ellipse cx="7" cy="7" rx="2.4" ry="5.6" fill="none" stroke="#2f5d1f" stroke-width="1"/><line x1="1.4" y1="7" x2="12.6" y2="7" stroke="#2f5d1f" stroke-width="1"/></svg>
          www.zub.capital
        </p>
      </div>
    </div>
  </section>

</body>
</html>
```